A slider bar and icons to be used on the map

#Background
We are currently creating a website for tourists to Japan . Named "Torii Path," It's a website where users can search for shrines and temples across Japan on the map. We are seeking designs for three icons(shrine icon, temple icon, and representing both shrine and temple icon) and a slider bar to be used on this site's map.
#Requirements
Cool and understandable icons and a slider bar that match the web design.
#Web Design Concept
Attached is a reference document.
#Desired Items
We need four items written below.
-Shrine icon
-Temple icon
-Icon representing both shrines and temples (expressed as a single icon)
-Slider bar
#Regarding the Slider Bar
It has two functions:
-Filter popular shrines and temples.
-Filiter shrines and temples with cool kanji.
We would like it to be able to filter from both the right and the left.
We want to express that moving to the right represents popularity or cool kanji. We'd like to express this on the slider bar as a design.
* reference> https://pics.example-lens.net/k7PqWx2mZ9vTbR4aN
Target Market(s)
Inbound tourists to Japan
Look and feel
Each slider illustrates characteristics of the customer's brand and the style your logo design should communicate.

```html
<!DOCTYPE html>
<html lang="en">
<head>
<meta charset="utf-8">
<title>Torii Path – Map Slider Bars</title>
<link rel="stylesheet" href="https://fonts.googleapis.com/css2?family=Barlow:wght@400;500&display=swap">
<style>
  :root {
    --bg: #ffffff;
    --icon-fill: #d6d7d9;
    --track-grey: #d1d2d4;
    --track-light: #e6e7e8;
    --track-edge: #a7a9ac;
    --knob-edge: #a7a9ac;
    --select-green: #00a14b;
    --option-bg: #e6e7e8;
    --option-text: #6d6e71;
    --box-edge: #bcbec0;
    --green: #3a8c4a;
    --gold: #fbc315;
    --orange: #f39a3b;
    --red: #ef4136;
    --mid-orange: #f7941d;
    --yellow: #fff200;
  }
  * { margin: 0; padding: 0; box-sizing: border-box; }
  html, body { width: 1200px; height: 1200px; overflow: hidden; background: var(--bg); }
  .canvas { position: relative; width: 1200px; height: 1200px; font-family: "Barlow", sans-serif; }

  .track {
    position: absolute; height: 25px; border-radius: 13px;
    overflow: hidden; border: 1px solid var(--track-edge);
  }
  .track--light { border-color: transparent; background: var(--track-light); }
  .track--grey { background: var(--track-grey); }
  .track__fill { position: absolute; left: 0; top: 0; bottom: 0; }
  .track__fill--cool { background: linear-gradient(90deg, var(--green) 0%, var(--gold) 45%, var(--orange) 100%); }
  .track__fill--warm {
    background: linear-gradient(90deg, var(--red) 0%, var(--mid-orange) 40%, var(--yellow) 90%, var(--gold) 100%);
    border: 1px solid var(--track-edge); border-radius: 13px 0 0 13px;
  }

  .knob {
    position: absolute; width: 42px; height: 42px; border-radius: 50%;
    background: #fff; border: 1px solid var(--knob-edge);
  }

  .icon-slot { position: absolute; background: var(--icon-fill); border-radius: 4px; }

  .menu { position: absolute; width: 146px; }
  .menu__item {
    height: 29px; border: 1px solid var(--box-edge);
    font-size: 20px; line-height: 27px; padding-left: 9px;
    color: var(--option-text); background: var(--option-bg);
    margin-bottom: 4px; letter-spacing: 0.3px; white-space: nowrap;
  }
  .menu__item--select { color: var(--select-green); background: #fff; font-weight: 500; margin-bottom: 5px; }
</style>
</head>
<body>
<main class="canvas">
  <!-- Slider one: single handle -->
  <div class="icon-slot" role="img" aria-label="Shrine icon" style="left:709px;top:107px;width:52px;height:49px"></div>
  <div class="track track--grey" style="left:136px;top:179px;width:946px">
    <div class="track__fill track__fill--cool" style="width:600px"></div>
  </div>
  <div class="knob" style="left:712px;top:170px"></div>
  <div class="menu" style="left:132px;top:217px">
    <div class="menu__item menu__item--select">Select</div>
    <div class="menu__item">Popularity</div>
    <div class="menu__item">Stylish Kanji</div>
  </div>

  <!-- Slider two: temple to shrine -->
  <div class="icon-slot" role="img" aria-label="Temple icon" style="left:133px;top:389px;width:50px;height:50px"></div>
  <div class="icon-slot" role="img" aria-label="Shrine icon" style="left:1019px;top:398px;width:52px;height:50px"></div>
  <div class="track track--light" style="left:131px;top:457px;width:945px">
    <div class="track__fill track__fill--warm" style="width:600px"></div>
  </div>
  <div class="knob" style="left:705px;top:446px"></div>
  <div class="menu" style="left:132px;top:489px">
    <div class="menu__item menu__item--select">Select</div>
    <div class="menu__item">Popularity</div>
    <div class="menu__item">Stylish Kanji</div>
  </div>

  <!-- Slider three: filters on both ends -->
  <div class="icon-slot" role="img" aria-label="Temple icon" style="left:129px;top:717px;width:50px;height:51px"></div>
  <div class="icon-slot" role="img" aria-label="Shrine icon" style="left:1014px;top:726px;width:52px;height:50px"></div>
  <div class="track track--light" style="left:126px;top:785px;width:946px">
    <div class="track__fill track__fill--warm" style="width:600px"></div>
  </div>
  <div class="knob" style="left:700px;top:775px"></div>
  <div class="menu" style="left:128px;top:817px">
    <div class="menu__item menu__item--select">Select</div>
    <div class="menu__item">Popularity</div>
    <div class="menu__item">Stylish Kanji</div>
  </div>
  <div class="menu" style="left:921px;top:830px">
    <div class="menu__item menu__item--select">Select</div>
    <div class="menu__item">Popularity</div>
    <div class="menu__item">Stylish Kanji</div>
  </div>
</main>
</body>
</html>
```